Brightwave Reach - Business Card

We need a business card for a Social Media Marketing company that specializes in online marketing for small businesses in Canada using common Social Media platforms such as Pixlora, Chatterly, Blinkpost & Quibber.

I have uploaded a copy of our logo which I would like utilized in the business card. We would like the business card to be modern yet classy design.

Our website is www.brightwavereach.ca

Industry/Entity Type

Marketing

Contact Information for Business Card

Email: info@brightwavereach.ca
Website: www.brightwavereach.ca
Telephone: 604-555-0193

Colors

Designer to choose colors to be used in the design.

Requirements
Must have
• Social Media icons on reverse
• Please add some designs with color.

```html
<!DOCTYPE html>
<html lang="en">
<head>
<meta charset="utf-8">
<title>Brightwave Reach – Business Card</title>
<link rel="stylesheet" href="https://fonts.googleapis.com/css2?family=Roboto:wght@400;500&family=Roboto+Condensed:wght@500;700&display=swap">
<style>
  :root {
    --backdrop: #e4e4e3;
    --card-white: #f6f6f6;
    --card-dark: #3a3d40;
    --ink: #3d3f42;
    --ink-soft: #9a9b9d;
    --band-grey: #a9aaab;
    --leaf-tone: #57595c;
    --paper-white: #ffffff;
    --rule: #c9cacb;
  }
  * { margin: 0; padding: 0; box-sizing: border-box; }
  html, body { width: 1200px; height: 960px; overflow: hidden; }
  body { background: var(--backdrop); font-family: "Roboto", Arial, sans-serif; position: relative; }

  .card { position: absolute; width: 600px; height: 344px; overflow: hidden; }
  .card--front { left: 314px; top: 113px; background: var(--card-white); }
  .card--back { left: 311px; top: 472px; background: var(--card-dark); }

  .brand-mark {
    position: absolute; left: 42px; top: 70px;
    font-family: "Roboto Condensed", Arial, sans-serif; font-weight: 700;
    font-size: 30px; line-height: 30px; color: var(--ink); text-align: center;
    letter-spacing: 0.5px; width: 180px;
  }

  .contact { position: absolute; right: 32px; top: 190px; text-align: right; color: var(--ink); }
  .contact__name { font-family: "Roboto Condensed", Arial, sans-serif; font-weight: 500; font-size: 21px; line-height: 26px; }
  .contact__role { font-size: 15px; color: var(--ink-soft); margin-top: 6px; letter-spacing: 0.3px; }
  .contact__line { font-size: 14px; margin-top: 8px; display: flex; justify-content: flex-end; align-items: center; gap: 8px; }
  .contact__line svg { width: 12px; height: 12px; fill: var(--ink); }
  .contact__line + .contact__line { margin-top: 4px; }

  .strip-grey { position: absolute; left: 0; bottom: 0; width: 340px; height: 14px; background: var(--band-grey); }
  .band-web {
    position: absolute; right: 0; bottom: 0; width: 272px; height: 36px;
    background: var(--ink); clip-path: polygon(32px 0, 100% 0, 100% 100%, 0 100%);
    color: var(--paper-white); font-size: 14px; letter-spacing: 1.4px;
    display: flex; align-items: center; justify-content: flex-end; padding-right: 30px;
  }

  .leaf-area {
    position: absolute; left: 8px; top: 8px; width: 264px; height: 330px;
    background: radial-gradient(ellipse at 50% 45%, var(--leaf-tone) 0%, rgba(87,89,92,0.5) 55%, rgba(58,61,64,0) 75%);
  }
  .back-brand {
    position: absolute; left: 280px; top: 196px; width: 290px; text-align: center;
    font-family: "Roboto Condensed", Arial, sans-serif; font-weight: 700;
    font-size: 42px; line-height: 38px; color: var(--paper-white); letter-spacing: 0.5px;
  }
  .social-row {
    position: absolute; left: 280px; top: 290px; width: 300px;
    display: flex; align-items: center; gap: 8px;
  }
  .social-row__rule { flex: 1; height: 1px; background: var(--rule); }
  .social-row__name { font-size: 11px; color: var(--paper-white); letter-spacing: 0.4px; }
</style>
</head>
<body>
  <section class="card card--front" aria-label="Card front">
    <div class="brand-mark">BRIGHTWAVE<br>REACH</div>
    <div class="contact">
      <div class="contact__name">EVAN MARLOW</div>
      <div class="contact__role">CEO/FOUNDER</div>
      <div class="contact__line">604-555-0193
        <svg viewBox="0 0 24 24" aria-hidden="true"><path d="M6.6 10.8a15.1 15.1 0 0 0 6.6 6.6l2.2-2.2c.3-.3.7-.4 1-.2 1.1.4 2.3.6 3.6.6.6 0 1 .4 1 1V20c0 .6-.4 1-1 1A17 17 0 0 1 3 4c0-.6.4-1 1-1h3.5c.6 0 1 .4 1 1 0 1.3.2 2.5.6 3.6.1.3 0 .7-.2 1z"/></svg>
      </div>
      <div class="contact__line">info@brightwavereach.ca
        <svg viewBox="0 0 24 24" aria-hidden="true"><path d="M2 5h20v14H2z M3 6l9 7 9-7" fill="none" stroke="currentColor"/><path d="M2 5h20v14H2zM4 7v.3l8 6 8-6V7l-8 6z"/></svg>
      </div>
    </div>
    <div class="strip-grey"></div>
    <div class="band-web">www.brightwavereach.ca</div>
  </section>

  <section class="card card--back" aria-label="Card back">
    <div class="leaf-area" role="img" aria-label="Large distressed maple leaf decoration"></div>
    <div class="back-brand">BRIGHTWAVE<br>REACH</div>
    <div class="social-row">
      <span class="social-row__rule"></span>
      <span class="social-row__name">Chatterly</span>
      <span class="social-row__name">Pixlora</span>
      <span class="social-row__name">Quibber</span>
      <span class="social-row__rule"></span>
    </div>
  </section>
</body>
</html>
```